House-share and Room Rental Website (With Focus on the Bedroom Landing Page)

Looking for website design for our House-share (executive accommodation) and room rental business.

Our company name is: Lodgivo could also be written as LodGivo or lodgivo. Either is fine .. just looking for a nice clean catchy logo to go with the design.

EXAMPLES
These are examples of other websites in this field that are doing well. this is a kind of baseline.
https://nestpartners-example.com.au/
https://www.bunkora-example.com/
https://www.dwelzy-example.com/
https://www.habiquo-example.net/
https://www.cohabiscout-example.com.au/

Our business model is to rent rooms to people looking for high-quality accommodation. We fill the gap between those looking to rent rooms and those with rooms to rent. However, our model is slightly different from those already on the market as we looking to fill a massive gap in the market delivering upmarket rooms for rent.(Executive Accommodation) also in the back end will be coupled with a self management process in the back end.

We offer executive style accommodation that stands out above the rest. With special extras like fire safety.. and management processes that create happier homes. We are looking for a web design package that can help us grow and scale our business. We need a design that is captivating

Our MAIN focus is having a room landing page that stands out from the rest... The core of our business will rely on the promotion of the rooms in a share house... so the whole design relies on the BEDROOM landing page to drive results.

Target Market(s)

We have 2 markets we are aiming at ... the first market is people offering rooms to rent who want the highest rental return. The second market is people looking to rent safe, high-quality rooms, in houses that are well managed and looked after.

Industry/Entity Type

Share Economy

Logo Text

LodGivo

Number of Pages Required

5+ page

Font styles to use
Sans Serif

Colors
3276b5

Requirements
Must have
• A messaging system whereby we can create direct communication between those offering rooms and those looking for rooms.
• A call to action that says " Schedule an Inspection"
• Landing page for promoting rooms
• A home page for showing stock.
• Profile page for those selling rooms
• Profile page for those looking for rooms.
• A scheduling calendar for booking inspections
Nice to have
• Pages where new residents can lock in a room.. pay bond and rents.. and sign contracts
• Notifications
• SMS capabilities in the backend.
Should not have
• No script or handwriting fonts.

```html
<!DOCTYPE html>
<html lang="en">
<head>
<meta charset="utf-8">
<title>LodGivo — Bedrooms</title>
<link href="https://fonts.googleapis.com/css2?family=Roboto:wght@400;500;700;900&family=Lato:wght@400;700&display=swap" rel="stylesheet">
<style>
:root{
  --sky:#0ea5e6;
  --brand:#3276b5;
  --btn:#1c86e8;
  --red:#e0231f;
  --ink:#1f2329;
  --muted:#8a8f98;
  --line:#e6e9ee;
  --card:#f3f5f8;
  --green:#3fae4a;
  --orange:#f29a1d;
  --dark:#262626;
  --darker:#1c1c1c;
}
*{box-sizing:border-box;margin:0;padding:0}
html,body{width:1200px;height:3600px;overflow:hidden;background:#fff}
body{position:relative;font-family:"Roboto",Arial,sans-serif;color:var(--ink)}
.abs{position:absolute}
.photo{position:absolute}

/* header */
.site-header{left:72px;top:0;width:1049px;height:67px;background:#fff;display:flex;align-items:center}
.brand-name{font-size:34px;font-weight:900;color:var(--red);margin-left:170px;letter-spacing:-.5px}
.main-nav{display:flex;gap:34px;margin-left:78px;font-size:11px;font-weight:700;text-transform:uppercase}
.login-link{margin-left:auto;margin-right:60px;font-size:11px;font-weight:700}

.search-band{left:72px;top:67px;width:1049px;height:53px;background:var(--sky);display:flex;align-items:center;justify-content:center}
.search-bar{display:flex;height:34px;background:#fff;border-radius:3px;overflow:hidden;width:650px}
.search-field{flex:1;display:flex;align-items:center;gap:8px;padding:0 14px;font-size:12px;color:#555;border-right:1px solid var(--line)}
.search-field.narrow{flex:0 0 120px;justify-content:space-between}
.search-go{width:55px;background:#222;color:#fff;font-size:11px;font-weight:700;display:flex;align-items:center;justify-content:center}

.hero-photo{left:72px;top:120px;width:1049px;height:391px;background:linear-gradient(120deg,#6f6a4e 0%,#b9a77e 35%,#e8dcc0 55%,#9f7a5a 80%,#4e3d2f 100%)}
.hero-dots{left:566px;top:494px;display:flex;gap:7px}
.hero-dots i{width:10px;height:10px;border-radius:50%;background:rgba(255,255,255,.6)}
.hero-dots i:first-child{background:#fff}
.listing-pop{left:511px;top:216px;width:286px;height:156px;background:#fff;border-radius:8px;box-shadow:0 6px 20px rgba(0,0,0,.25);padding:14px;display:flex;gap:14px}
.listing-pop .thumb{width:130px;height:110px;border-radius:6px;background:linear-gradient(160deg,#9fc3e0,#d8e3ea 55%,#7d6a54)}
.listing-pop .price{font-size:18px;font-weight:700}
.listing-pop .name{font-size:13px;font-weight:700;margin-top:6px;line-height:1.25}
.listing-pop .addr{font-size:9px;color:var(--muted);margin-top:6px}
.listing-pop .details{font-size:9px;margin-top:8px;font-weight:700}
.listing-pop .view{position:absolute;right:14px;bottom:12px;background:#222;color:#fff;font-size:8px;padding:5px 12px;border-radius:3px;font-weight:700}

.feature-band{left:72px;top:511px;width:1049px;height:221px;background:var(--sky);color:#fff}
.feature{position:absolute;top:16px;width:240px;text-align:center}
.feature .ring{width:76px;height:76px;border:3px solid #fff;border-radius:50%;margin:0 auto;display:flex;align-items:center;justify-content:center}
.feature h3{font-size:15px;font-weight:700;margin-top:16px}
.feature p{font-size:11px;line-height:1.45;margin-top:6px;opacity:.9;padding:0 30px}

/* section headings */
.section-title{left:0;width:1200px;text-align:center;font-size:19px;font-weight:700}
.section-sub{left:0;width:1200px;text-align:center;font-size:11px;color:var(--muted)}

/* room cards */
.room-card{position:absolute;background:var(--card)}
.room-card .shot{position:relative;width:100%}
.room-card .tag{position:absolute;right:10px;top:10px;font-size:7px;font-weight:700;color:#fff;padding:4px 8px;background:var(--green);text-transform:uppercase}
.room-card .tag.hot{background:var(--orange)}
.room-card .price{position:absolute;left:10px;bottom:10px;font-size:11px;font-weight:700;color:#fff;background:rgba(0,0,0,.6);padding:4px 8px;border-radius:2px}
.room-card .body{background:#fff;padding:14px 10px 10px}
.room-card .loc{font-size:8px;color:#555;display:flex;gap:5px;align-items:center;text-transform:uppercase}
.room-card h4{font-size:14px;font-weight:500;margin-top:8px}
.room-card .meta{display:flex;gap:14px;font-size:8px;color:var(--muted);padding:10px;background:var(--card)}

.btn-pill{background:var(--btn);color:#fff;font-weight:700;text-transform:uppercase;border-radius:22px;display:flex;align-items:center;justify-content:center}

/* stats */
.stat{display:flex;align-items:center;gap:14px}
.stat b{display:block;font-size:28px;color:var(--btn);font-weight:900;line-height:1}
.stat span{font-size:10px;font-weight:700}

/* responsibility */
.agent-photo{left:72px;top:2208px;width:480px;height:408px;background:radial-gradient(circle at 50% 45%,#c9ccd1 0%,#eef0f2 55%,#fff 78%)}
.promo{left:614px;top:2268px;width:400px}
.promo h2{font-size:23px;font-weight:700;line-height:1.2}
.promo p{font-size:11px;line-height:1.6;color:#555;margin-top:16px}
.contact-form{display:grid;grid-template-columns:1fr 1fr;gap:8px 8px;margin-top:20px}
.contact-form span{background:var(--card);border:1px solid var(--line);height:30px;font-size:9px;color:#777;display:flex;align-items:center;padding:0 10px;font-style:italic}

/* testimonials */
.review{position:absolute;width:220px;font-family:"Lato",sans-serif}
.review .avatar{width:46px;height:46px;border-radius:50%;background:linear-gradient(#c8cfd6,#9aa4ae)}
.review p{font-size:11px;line-height:1.5;margin-top:18px;color:#333}
.review .who{margin-top:14px;font-size:10px;color:var(--btn);font-weight:700}
.review .role{font-size:9px;color:var(--muted)}
.review .quote{position:absolute;right:0;bottom:0;font-size:50px;color:#e3e6ea;font-weight:900;line-height:.6}
.scroll-dots{display:flex;flex-direction:column;gap:5px}
.scroll-dots i{width:6px;height:6px;border-radius:50%;background:#b7bcc4}
.scroll-dots i:nth-child(2){background:var(--btn)}

/* gallery */
.gallery{left:72px;top:2988px;width:1049px;height:204px;display:flex}
.gallery .tile{flex:1;position:relative}
.gallery .cap{position:absolute;left:18px;bottom:24px;color:#fff;font-size:10px;font-weight:700;line-height:1.3}

/* footer */
.social-bar{left:72px;top:3192px;width:1049px;height:53px;background:var(--darker);display:flex;justify-content:space-around;align-items:center}
.social-bar i{width:14px;height:14px;border-radius:50%;background:#bfbfbf}
.footer{left:72px;top:3245px;width:1049px;height:355px;background:var(--dark);color:#cfcfcf}
.footer .brand-name{position:absolute;left:58px;top:30px;margin:0;font-size:26px}
.footer .about{position:absolute;left:48px;top:78px;width:250px;font-size:9px;line-height:1.6;color:#aaa}
.footer h5{color:#fff;font-size:13px;font-weight:700}
.links{position:absolute;left:48px;top:170px}
.links ul{list-style:none;display:grid;grid-template-columns:130px 130px;gap:6px;margin-top:14px;font-size:9px;color:#bbb}
.posts{position:absolute;left:412px;top:30px;width:340px}
.post{display:flex;gap:12px;margin-top:18px}
.post .pic{width:90px;height:68px;background:linear-gradient(135deg,#f2a6c9,#e85aa0)}
.post .pic.b{background:linear-gradient(135deg,#cfa478,#6e4b33)}
.post b{display:block;color:#fff;font-size:12px}
.post .t{font-size:10px;color:#fff;font-weight:700;margin-top:6px}
.post .a{font-size:8px;color:#999;margin-top:6px}
.copyright{position:absolute;left:0;bottom:8px;width:100%;text-align:center;font-size:9px;color:#999}
.cta-inspection{left:552px;top:3521px;width:216px;height:32px;background:var(--red);color:#fff;font-weight:900;font-size:14px;text-transform:uppercase;display:flex;align-items:center;justify-content:center;letter-spacing:.3px}

/* chat */
.chat{left:792px;top:3139px;width:317px;height:461px;background:#fff;border:1px solid #d5d9df;box-shadow:0 4px 18px rgba(0,0,0,.18)}
.chat-head{height:56px;background:var(--btn);color:#fff;display:flex;align-items:center;padding:0 26px;font-size:18px;font-weight:500}
.chat-head .ctrl{margin-left:auto;font-size:18px;letter-spacing:10px}
.bubble{position:absolute;font-size:12px;padding:8px 12px;border-radius:3px}
.bubble.them{background:#e3e6ea;left:18px}
.bubble.me{background:#53aee8;color:#fff;right:24px}
.chat-input{position:absolute;left:10px;right:10px;bottom:10px;height:44px;border:1px solid #d5d9df;display:flex;align-items:center;padding-left:12px;font-size:10px;color:#999}
.chat-input .send{margin-left:auto;width:40px;height:42px;background:var(--btn);display:flex;align-items:center;justify-content:center}
</style>
</head>
<body>

<header class="site-header abs">
  <div class="brand-name">LodGivo</div>
  <nav class="main-nav"><span>Home</span><span>About Us</span><span>Contact Us</span><span>Bedrooms</span><span>Child Rooms</span><span>Blog</span></nav>
  <div class="login-link">LOGIN / REGISTER</div>
</header>

<div class="search-band abs">
  <div class="search-bar">
    <div class="search-field"><svg width="12" height="12" viewBox="0 0 12 12"><circle cx="5" cy="5" r="4" fill="none" stroke="#333" stroke-width="1.6"/><path d="M8 8l3 3" stroke="#333" stroke-width="1.6"/></svg>Keywords</div>
    <div class="search-field narrow">Select Room <span>▾</span></div>
    <div class="search-field narrow">Room Style <span>▾</span></div>
    <div class="search-go">GO</div>
  </div>
</div>

<div class="hero-photo photo" role="img" aria-label="Luxurious bedroom interior with a tufted bed, chandelier and patterned wallpaper"></div>
<div class="listing-pop abs">
  <div class="thumb" role="img" aria-label="Modern family house exterior"></div>
  <div>
    <div class="price">$125,799</div>
    <div class="name">Amazing Family<br>Bed Room</div>
    <div class="addr">Maple Court, Eastvale</div>
    <div class="details">Details ▸</div>
  </div>
  <div class="view">FOR VIEW</div>
</div>
<div class="hero-dots abs"><i></i><i></i><i></i><i></i><i></i></div>

<section class="feature-band abs">
  <div class="feature" style="left:144px">
    <div class="ring"><svg width="34" height="34" viewBox="0 0 34 34" fill="none" stroke="#fff" stroke-width="2"><rect x="5" y="6" width="14" height="24"/><rect x="19" y="14" width="10" height="16"/><path d="M9 11h6M9 16h6M9 21h6M23 19h2M23 24h2"/></svg></div>
    <h3>Modern Rooms</h3>
    <p>Well-planned spaces finished to a high standard for easy living.</p>
  </div>
  <div class="feature" style="left:408px">
    <div class="ring"><svg width="34" height="34" viewBox="0 0 34 34" fill="none" stroke="#fff" stroke-width="2"><path d="M8 8l18 18M26 8L8 26"/><circle cx="8" cy="8" r="3"/><circle cx="26" cy="26" r="3"/></svg></div>
    <h3>Fire Protection Services</h3>
    <p>Every house is checked and fitted with tested safety gear.</p>
  </div>
  <div class="feature" style="left:672px">
    <div class="ring"><svg width="34" height="34" viewBox="0 0 34 34" fill="none" stroke="#fff" stroke-width="2"><path d="M5 16L17 6l12 10v13H5z"/><circle cx="17" cy="20" r="4"/></svg></div>
    <h3>Child Rooms</h3>
    <p>We have bright, safe and comfy rooms for your children.</p>
  </div>
</section>

<h2 class="section-title abs" style="top:796px">Newest Bedroom</h2>
<p class="section-sub abs" style="top:824px">Absolutely Stunning Design and Functionality</p>

<!-- newest row 1 -->
<article class="room-card" style="left:211px;top:871px;width:377px">
  <div class="shot" style="height:281px;background:linear-gradient(135deg,#4a3a2a,#c99a55 45%,#e8c98a 60%,#5b4532)" role="img" aria-label="Warm-lit bedroom with a golden bedspread"><span class="tag">For Rent</span><span class="price">$625,000</span></div>
  <div class="body"><div class="loc">📍 27 Harbour Lane, Rivergate</div><h4>Small cottage in Upper New</h4></div>
  <div class="meta"><span>▦ 4 Beds</span><span>▬ 2 Bath</span><span>◌ 1 pool</span><span>⌂ 2 Garages</span></div>
</article>
<article class="room-card" style="left:607px;top:871px;width:377px">
  <div class="shot" style="height:281px;background:linear-gradient(135deg,#8fa7b8,#e7ecef 45%,#bfd4e0 65%,#4f5c66)" role="img" aria-label="Cool-toned modern bedroom with a lounge chair"><span class="tag">For Rent</span><span class="price">$625,000</span></div>
  <div class="body"><div class="loc">📍 27 Harbour Lane, Rivergate</div><h4>Small cottage in Upper New</h4></div>
  <div class="meta"><span>▦ 4 Beds</span><span>▬ 2 Bath</span><span>◌ 1 pool</span><span>⌂ 2 Garages</span></div>
</article>

<!-- newest row 2 -->
<article class="room-card" style="left:214px;top:1274px;width:244px">
  <div class="shot" style="height:159px;background:linear-gradient(135deg,#2e2e33,#8a8f98 50%,#d9d3c8)" role="img" aria-label="Dark contemporary bedroom"><span class="tag hot">For Sale</span><span class="price">$625,000</span></div>
  <div class="body"><div class="loc">📍 Maple Court, Eastvale</div><h4>Villa On Washington Ave</h4></div>
  <div class="meta"><span>▦ 4 Beds</span><span>▬ 2 Bath</span><span>◌ 1 pool</span><span>⌂ 2</span></div>
</article>
<article class="room-card" style="left:478px;top:1274px;width:242px">
  <div class="shot" style="height:159px;background:linear-gradient(135deg,#dfe5ea,#ffffff 45%,#a9b6c0)" role="img" aria-label="Bright white bedroom with large windows"><span class="tag">For Rent</span><span class="price">$625,000</span></div>
  <div class="body"><div class="loc">📍 Maple Court, Eastvale</div><h4>Villa On Washington Ave</h4></div>
  <div class="meta"><span>▦ 4 Beds</span><span>▬ 2 Bath</span><span>◌ 1 pool</span><span>⌂ 2</span></div>
</article>
<article class="room-card" style="left:739px;top:1274px;width:245px">
  <div class="shot" style="height:159px;background:linear-gradient(135deg,#c9b8d8,#f0e4ef 50%,#a98fb8)" role="img" aria-label="Lilac bedroom with soft lighting"><span class="tag">For Rent</span><span class="price">$625,000</span></div>
  <div class="body"><div class="loc">📍 Maple Court, Eastvale</div><h4>Villa On Washington Ave</h4></div>
  <div class="meta"><span>▦ 4 Beds</span><span>▬ 2 Bath</span><span>◌ 1 pool</span><span>⌂ 2</span></div>
</article>

<div class="btn-pill abs" style="left:528px;top:1595px;width:149px;height:36px;font-size:13px">View All Rooms</div>

<!-- stats -->
<div class="stat abs" style="left:240px;top:1742px"><svg width="36" height="40" viewBox="0 0 36 40" fill="none" stroke="#222" stroke-width="2"><circle cx="18" cy="15" r="11"/><circle cx="18" cy="15" r="6"/><path d="M11 24l-4 13 6-3 3 5 2-8M25 24l4 13-6-3-3 5-2-8"/></svg><div><b>3587</b><span>Satisfied Clients</span></div></div>
<div class="stat abs" style="left:432px;top:1742px"><svg width="36" height="40" viewBox="0 0 36 40" fill="#222"><circle cx="18" cy="10" r="8"/><path d="M4 40c0-12 6-19 14-19s14 7 14 19z"/></svg><div><b>70</b><span>Employees</span></div></div>
<div class="stat abs" style="left:624px;top:1742px"><svg width="40" height="40" viewBox="0 0 40 40" fill="#222"><path d="M4 14h26v10a10 10 0 0 1-10 10h-6A10 10 0 0 1 4 24z"/><path d="M30 17h3a4 4 0 0 1 0 8h-3" fill="none" stroke="#222" stroke-width="3"/><rect x="2" y="35" width="32" height="3"/></svg><div><b>685</b><span>Cups of Coffee</span></div></div>
<div class="stat abs" style="left:840px;top:1742px"><svg width="40" height="40" viewBox="0 0 40 40" fill="#222"><path d="M20 3L2 18h5v18h26V18h5z"/><path d="M14 28l5 4 8-10" fill="none" stroke="#fff" stroke-width="3"/></svg><div><b>2930</b><span>Total Rooms</span></div></div>

<h2 class="section-title abs" style="top:1843px">Child Bedroom</h2>
<p class="section-sub abs" style="top:1871px">This is our child bedroom for your children</p>

<article class="room-card" style="left:214px;top:1927px;width:244px">
  <div class="shot" style="height:157px;background:linear-gradient(135deg,#f7b8d6,#fde6f1 45%,#e76aa5)" role="img" aria-label="Pink child bedroom with canopy bed"><span class="tag hot">For Sale</span><span class="price">$625,000</span></div>
  <div class="body"><div class="loc">📍 Maple Court, Eastvale</div><h4>Two Child Bedroom</h4></div>
  <div class="meta"><span>▦ 4 Beds</span><span>▬ 2 Bath</span><span>◌ 1 pool</span><span>⌂ 2</span></div>
</article>
<article class="room-card" style="left:478px;top:1927px;width:242px">
  <div class="shot" style="height:157px;background:linear-gradient(135deg,#cfe9e6,#f5f7f4 50%,#7fc0bd)" role="img" aria-label="Mint-toned child bedroom with twin beds"><span class="tag">For Rent</span><span class="price">$625,000</span></div>
  <div class="body"><div class="loc">📍 Maple Court, Eastvale</div><h4>Two Child Bedroom</h4></div>
  <div class="meta"><span>▦ 4 Beds</span><span>▬ 2 Bath</span><span>◌ 1 pool</span><span>⌂ 2</span></div>
</article>
<article class="room-card" style="left:739px;top:1927px;width:245px">
  <div class="shot" style="height:157px;background:linear-gradient(135deg,#f9c3dc,#f48cbc 50%,#c9477f)" role="img" aria-label="Bright pink girl's bedroom"><span class="tag">For Rent</span><span class="price">$625,000</span></div>
  <div class="body"><div class="loc">📍 Maple Court, Eastvale</div><h4>Two Child Bedroom</h4></div>
  <div class="meta"><span>▦ 4 Beds</span><span>▬ 2 Bath</span><span>◌ 1 pool</span><span>⌂ 2</span></div>
</article>
<div class="scroll-dots abs" style="left:1037px;top:2012px"><i></i><i></i><i></i></div>

<!-- responsibility -->
<div class="agent-photo photo" role="img" aria-label="Smiling property agent in a cardigan offering a handshake"></div>
<section class="promo abs">
  <h2>This is Our Responsibility To<br>Give Comfortable Rooms</h2>
  <p>Every home we list is inspected, well kept and fully managed, so tenants feel safe and owners get the best return from each room. Book a visit and see the standard for yourself.</p>
  <div class="contact-form"><span>Services</span><span>Name</span><span>Email</span><span>Phone Number</span></div>
  <div class="btn-pill" style="width:166px;height:34px;font-size:11px;margin-top:28px;text-transform:none">Contact With us</div>
</section>

<!-- testimonials -->
<h2 class="section-title abs" style="top:2654px">Our Customar Says</h2>
<p class="section-sub abs" style="top:2682px">Absolutely Stunning Design and Functionality</p>
<div class="review" style="left:240px;top:2706px">
  <div class="avatar" role="img" aria-label="Customer portrait"></div>
  <p>"The room was spotless and the house ran smoothly. Booking an inspection took minutes and the team answered every question fast."</p>
  <div class="who">Owen Castell</div><div class="role">Tenant, Rivergate</div><span class="quote">“</span>
</div>
<div class="review" style="left:504px;top:2706px">
  <div class="avatar" role="img" aria-label="Customer portrait"></div>
  <p>"My rooms now earn more than ever and I never chase rent. The safety checks give my tenants real peace of mind."</p>
  <div class="who">Reid Malone</div><div class="role">Room Owner, Eastvale</div><span class="quote">“</span>
</div>
<div class="review" style="left:768px;top:2706px">
  <div class="avatar" role="img" aria-label="Customer portrait"></div>
  <p>"Lovely quiet home with great housemates. Messaging the owner directly made moving in simple and stress free."</p>
  <div class="who">Theo Barnard</div><div class="role">Tenant, Harbour Lane</div><span class="quote">“</span>
</div>
<div class="scroll-dots abs" style="left:1037px;top:2850px"><i></i><i></i><i></i></div>

<!-- gallery -->
<div class="gallery abs">
  <div class="tile" style="background:linear-gradient(135deg,#7fa34a,#d9c9a3 60%,#8c6a4a)" role="img" aria-label="Colourful kids bedroom"><div class="cap">LIFESTYLE<br>Developing a lifestyle</div></div>
  <div class="tile" style="background:linear-gradient(135deg,#9bc4e2,#e9f1f6 55%,#6d8fa8)" role="img" aria-label="Bedroom with blue drapes"><div class="cap">LIFESTYLE<br>Developing a lifestyle</div></div>
  <div class="tile" style="background:linear-gradient(135deg,#5a4534,#c8a070 55%,#3d2e22)" role="img" aria-label="Warm-toned master bedroom"><div class="cap">LIFESTYLE<br>Developing a strategy</div></div>
  <div class="tile" style="background:linear-gradient(135deg,#b8c4cc,#eef2f4 55%,#7a8c98)" role="img" aria-label="Minimal grey bedroom"></div>
</div>

<div class="social-bar abs"><i></i><i></i><i></i><i></i><i></i><i></i></div>

<footer class="footer abs">
  <div class="brand-name">LodGivo</div>
  <p class="about">Quality shared homes and executive rooms, managed with care. Safe houses, happy residents and the best return for every owner.</p>
  <div class="links">
    <h5>More Information</h5>
    <ul><li>Help Center</li><li>About Lodgivo</li><li>Terms of Use</li><li>Careers</li><li>Lodgivo Blog</li><li>Terms of Use</li></ul>
  </div>
  <div class="posts">
    <h5>Popular Posts</h5>
    <div class="post"><div class="pic" role="img" aria-label="Pink bedroom thumbnail"></div><div><b>$125,799</b><div class="t">Amazing Apartment Family</div><div class="a">📍 Maple Court, Eastvale</div></div></div>
    <div class="post"><div class="pic b" role="img" aria-label="Wood-toned bedroom thumbnail"></div><div><b>$125,799</b><div class="t">Amazing Apartment Family</div><div class="a">📍 Maple Court, Eastvale</div></div></div>
  </div>
  <div class="copyright">© 2016, All Rights Reserved. Lodgivo.com</div>
</footer>
<div class="cta-inspection abs">Schedule an Inspection</div>

<!-- chat -->
<aside class="chat abs">
  <div class="chat-head">Welcome to TalkNest <span class="ctrl">_ ✕</span></div>
  <div class="bubble them" style="top:100px">Hi</div>
  <div class="bubble them" style="top:150px">How may I help you?</div>
  <div class="bubble me" style="top:194px">Hello</div>
  <div class="bubble me" style="top:236px">I need help with the design.</div>
  <div class="abs" style="left:14px;bottom:70px;font-size:12px;color:#666">🔈 🎙</div>
  <div class="chat-input">Type your message here…<span class="send"><svg width="18" height="18" viewBox="0 0 18 18"><path d="M1 2l16 7-16 7 3-7z" fill="#fff"/></svg></span></div>
</aside>

</body>
</html>
```